Veldmark Supplies Business Card

Professional business card that stand out to our potential customers. Front and back with clean modern design

Industry/Entity Type

Oil and gas

Contact Information for Business Card

Name, address, website , office phone and cell number

Requirements
Must have
• Editable files for each employee

```html
<!DOCTYPE html>
<html lang="en">
<head>
<meta charset="utf-8">
<title>Veldmark Supplies Business Card</title>
<link href="https://fonts.googleapis.com/css2?family=Montserrat:wght@400;500;700;800&display=swap" rel="stylesheet">
<style>
  :root {
    --red: #e82128;
    --blue: #0fb1d3;
    --white: #ffffff;
    --ink: #1d1d1d;
    --stage: #e9e6e1;
  }
  * { margin: 0; padding: 0; box-sizing: border-box; }
  html, body { width: 1200px; height: 931px; overflow: hidden; }
  body {
    background: var(--stage);
    font-family: "Montserrat", Arial, sans-serif;
    position: relative;
  }
  .card {
    position: absolute;
    width: 620px;
    height: 354px;
    border-radius: 22px;
    overflow: hidden;
    box-shadow: 0 10px 24px rgba(0,0,0,0.18);
  }

  /* Front */
  .card-front { left: 60px; top: 60px; background: var(--red); }
  .front-brand {
    position: absolute; left: 0; right: 0; top: 0; bottom: 0;
    display: flex; align-items: center; justify-content: center; gap: 16px;
  }
  .front-brand .mark { width: 44px; height: 44px; background: var(--white); }
  .front-brand .brand-name {
    color: var(--white); font-weight: 800; font-size: 38px;
    letter-spacing: 1px; text-transform: uppercase;
  }

  /* Back */
  .card-back { left: 520px; top: 517px; background: var(--white); }
  .back-brand {
    position: absolute; right: 34px; top: 72px;
    display: flex; align-items: center; gap: 10px;
  }
  .back-brand .mark { width: 24px; height: 24px; background: var(--red); }
  .back-brand .brand-name {
    color: var(--red); font-weight: 800; font-size: 21px;
    letter-spacing: 0.5px; text-transform: uppercase;
  }
  .rule {
    position: absolute; left: 98px; right: 34px; top: 190px;
    height: 1.5px; background: var(--red);
  }
  .person { position: absolute; left: 98px; top: 136px; }
  .person .name { color: var(--red); font-weight: 800; font-size: 26px; line-height: 1.1; }
  .person .title { color: var(--ink); font-weight: 400; font-size: 15px; margin-top: 2px; }
  .contacts {
    position: absolute; left: 98px; top: 200px;
    list-style: none; font-size: 14px; color: var(--ink);
  }
  .contacts li { display: flex; align-items: center; gap: 10px; height: 22px; }
  .contacts svg { width: 14px; height: 14px; fill: var(--blue); flex: none; }
  .address {
    position: absolute; right: 34px; top: 202px; text-align: right;
    font-size: 13px; line-height: 1.4; color: var(--ink);
  }
  .band-blue {
    position: absolute; left: 0; bottom: 0; width: 462px; height: 16px;
    background: var(--blue);
  }
  .band-red {
    position: absolute; right: 0; bottom: 0; width: 148px; height: 42px;
    background: var(--red);
  }
</style>
</head>
<body>

<section class="card card-front" aria-label="Card front">
  <div class="front-brand">
    <span class="mark"></span>
    <span class="brand-name">Veldmark Supplies</span>
  </div>
</section>

<section class="card card-back" aria-label="Card back">
  <div class="back-brand">
    <span class="mark"></span>
    <span class="brand-name">Veldmark Supplies</span>
  </div>

  <div class="person">
    <div class="name">Tomas Reyvik</div>
    <div class="title">President</div>
  </div>
  <div class="rule"></div>

  <ul class="contacts">
    <li>
      <svg viewBox="0 0 16 16" aria-hidden="true"><path d="M2 5c0-2 2-3 6-3s6 1 6 3v1h-3V5H5v1H2zM3 8h10l1 6H2zm5 1.5a2 2 0 1 0 0 4 2 2 0 0 0 0-4z"/></svg>
      +1.555.210.0400 x123
    </li>
    <li>
      <svg viewBox="0 0 16 16" aria-hidden="true"><path d="M3 1l3 3-2 2c1 2 3 4 5 5l2-2 3 3-2 3C7 14 2 9 1 3z"/></svg>
      +1.555.318.642
    </li>
    <li>
      <svg viewBox="0 0 16 16" aria-hidden="true"><path d="M1 3h14v10H1zm1 1v1l6 4 6-4V4z"/></svg>
      info@veldmarksupplies.com
    </li>
    <li>
      <svg viewBox="0 0 16 16" aria-hidden="true"><path d="M8 1a7 7 0 1 0 0 14A7 7 0 0 0 8 1zm0 1.5v11M2 8h12" stroke="#fff" stroke-width="1"/></svg>
      www.veldmarksupplies.com
    </li>
  </ul>

  <address class="address" style="font-style:normal">
    42 Ridgeline Plaza<br>
    Harlow Springs, NJ 07000 USA
  </address>

  <div class="band-blue"></div>
  <div class="band-red"></div>
</section>

</body>
</html>
```